Business Card Design needed for start up company Halvora

In need of a new business card designed for a start up company based in Sydney, Halvora is a new start up innovative Company, our mission it to make property accessible for everyday Australian and to become the leading Real Estate platform in Australia. We want it to be fresh and clean.

Industry/Entity Type

Financial

Contact Information for Business Card

Section for Name
Section for Title

HALVORA - The Strength of Pooling
Mobile:
Direct:

Font styles to use
Sans Serif

Colors
33a6d7
0692cd
0255a3
ffffff

Requirements
Must have
• Logo, all business card details

```html
<!DOCTYPE html>
<html lang="en">
<head>
<meta charset="utf-8">
<title>Halvora – Business Card</title>
<link rel="stylesheet" href="https://fonts.googleapis.com/css2?family=Open+Sans:wght@400;600;700;800&display=swap">
<style>
  :root {
    --stage: #161616;
    --paper: #eeede8;
    --navy: #1d4a7c;
    --brand-blue: #219cd7;
    --ink-blue: #1e4a80;
    --light-blue: #3a9fd4;
    --white: #ffffff;
  }
  * { margin: 0; padding: 0; box-sizing: border-box; }
  html, body { width: 1200px; height: 741px; overflow: hidden; }
  body {
    background: var(--stage);
    font-family: "Open Sans", sans-serif;
    position: relative;
  }
  .card {
    position: absolute;
    top: 229px;
    width: 495px;
    height: 282px;
    border-radius: 12px;
    overflow: hidden;
  }
  .card--front { left: 100px; background: var(--paper); }
  .card--back { left: 606px; background: var(--navy); }

  .half-disc {
    position: absolute;
    width: 304px;
    height: 304px;
    border-radius: 50%;
    background: var(--brand-blue);
    top: -10px;
  }
  .card--front .half-disc { left: 353px; }
  .card--back .half-disc { left: -153px; }

  .brand-dot {
    position: absolute;
    border-radius: 50%;
    background: var(--brand-blue);
  }
  .brand-name {
    position: absolute;
    font-weight: 800;
    letter-spacing: -0.5px;
    line-height: 1;
  }
  .brand-tagline {
    position: absolute;
    font-weight: 600;
    font-size: 14px;
    letter-spacing: 0.8px;
    white-space: nowrap;
  }

  .card--front .brand-dot { left: 20px; top: 22px; width: 86px; height: 86px; }
  .card--front .brand-name { left: 114px; top: 44px; font-size: 42px; color: var(--ink-blue); }
  .card--front .brand-tagline { left: 112px; top: 94px; color: var(--ink-blue); }

  .card--back .brand-dot { left: 210px; top: 164px; width: 80px; height: 80px; }
  .card--back .brand-name { left: 296px; top: 182px; font-size: 38px; color: var(--white); }
  .card--back .brand-tagline { left: 283px; top: 229px; font-size: 13px; color: var(--white); }

  .person { position: absolute; left: 22px; top: 147px; }
  .person__name { font-size: 17px; font-weight: 700; color: var(--ink-blue); line-height: 1.05; }
  .person__title { font-size: 14px; font-weight: 400; color: var(--light-blue); line-height: 1.1; }

  .contacts { position: absolute; left: 22px; top: 199px; list-style: none; }
  .contacts li {
    display: flex; align-items: center; gap: 6px;
    height: 18px; font-size: 13.5px; color: var(--ink-blue);
  }
  .contacts svg { width: 17px; height: 17px; flex: none; }
</style>
</head>
<body>

  <section class="card card--front" aria-label="Business card front">
    <div class="half-disc"></div>
    <div class="brand-dot"></div>
    <div class="brand-name">HALVORA</div>
    <div class="brand-tagline">The Strength of Pooling</div>

    <div class="person">
      <div class="person__name">LIAM CARTER</div>
      <div class="person__title">Managing Director</div>
    </div>

    <ul class="contacts">
      <li>
        <svg viewBox="0 0 18 18" aria-label="Mobile"><circle cx="9" cy="9" r="9" fill="#219cd7"/><rect x="6.2" y="4" width="5.6" height="10" rx="1.2" fill="none" stroke="#fff" stroke-width="1.3"/><line x1="8" y1="12" x2="10" y2="12" stroke="#fff" stroke-width="1"/></svg>
        0412 555 019
      </li>
      <li>
        <svg viewBox="0 0 18 18" aria-label="Direct"><circle cx="9" cy="9" r="9" fill="#219cd7"/><path d="M4.5 8 Q9 4.5 13.5 8 L12.5 9.5 L11 8.6 L11 7.6 Q9 7 7 7.6 L7 8.6 L5.5 9.5 Z" fill="#fff"/><rect x="6" y="10" width="6" height="3.5" rx="0.6" fill="#fff"/></svg>
        02 5550 1842
      </li>
      <li>
        <svg viewBox="0 0 18 18" aria-label="Email"><circle cx="9" cy="9" r="9" fill="#219cd7"/><rect x="4.5" y="5.8" width="9" height="6.4" rx="0.8" fill="#fff"/><path d="M4.8 6.2 L9 9.4 L13.2 6.2" fill="none" stroke="#219cd7" stroke-width="1"/></svg>
        liam@halvora.com.au
      </li>
    </ul>
  </section>

  <section class="card card--back" aria-label="Business card back">
    <div class="half-disc"></div>
    <div class="brand-dot"></div>
    <div class="brand-name">HALVORA</div>
    <div class="brand-tagline">The Strength of Pooling</div>
  </section>

</body>
</html>
```